Vantor Wear and Fuel is looking for a Clothing/Supplement Online Store Website!

Must be convenient, and user friendly, with vibrant colors that catch the eye!

Target Market(s)

Athletes, and Fashion Customers

Industry/Entity Type

Fitness

Coding

Coded - Design and coding required

Number of Pages Required

3 page

Font styles to use
Decorative

Colors

Designer to choose colors to be used in the design.

Requirements
Must have
• Somewhere to feature products, features to promote discounts and make announcements.
Nice to have
• My logos on each page

```html
<!DOCTYPE html>
<html lang="en">
<head>
<meta charset="utf-8">
<title>Vantor Wear and Fuel — Online Store</title>
<link href="https://fonts.googleapis.com/css2?family=Montserrat:wght@400;600;700;800&family=Open+Sans:wght@400;600;700&display=swap" rel="stylesheet">
<style>
:root{
  --ink:#1f1f1f;
  --dark:#262626;
  --darker:#1b1b1b;
  --nav:#2d2d2d;
  --muted:#6d6d6d;
  --line:#d9d9d9;
  --soft:#f1f1f1;
  --white:#ffffff;
  --star:#f2a413;
  --sale:#3fae49;
}
*{box-sizing:border-box;margin:0;padding:0}
html,body{width:1200px;height:3972px;overflow:hidden}
body{font-family:"Open Sans",Arial,sans-serif;color:var(--ink);background:var(--white);position:relative}
h1,h2,h3,h4,.nav a,.btn{font-family:"Montserrat",Arial,sans-serif}
.wrap{position:absolute;left:88px;right:88px}
.photo{display:block}

/* top bar */
.topbar{position:absolute;top:0;left:0;width:1200px;height:40px;background:var(--soft);font-size:13px;color:var(--muted)}
.topbar .lang{position:absolute;left:88px;top:11px;display:flex;gap:26px}
.topbar .links{position:absolute;right:88px;top:11px;display:flex;gap:26px}
.topbar .links span{display:flex;align-items:center;gap:6px}

/* header */
.header{position:absolute;top:40px;left:0;width:1200px;height:152px}
.brand{position:absolute;left:88px;top:50px;display:flex;align-items:center;gap:12px}
.brand-mark{width:34px;height:34px;background:var(--ink)}
.brand-name{font-family:"Montserrat",sans-serif;font-weight:800;font-size:30px;letter-spacing:1px;color:var(--ink)}
.head-info{position:absolute;top:62px;display:flex;align-items:center;gap:12px;font-size:13px;line-height:17px;color:var(--muted)}
.head-info b{color:var(--ink);font-weight:600}
.head-info.offer{left:740px}
.head-info.cart{left:990px}

/* nav */
.nav{position:absolute;top:192px;left:0;width:1200px;height:68px;background:var(--nav);display:flex;align-items:center;padding-left:88px}
.nav a{color:var(--white);text-decoration:none;font-size:17px;font-weight:600;padding:0 28px;height:68px;line-height:68px}
.nav a.active{background:var(--white);color:var(--ink)}
.nav .search{position:absolute;right:96px;top:22px}

/* hero */
.hero{position:absolute;top:260px;left:0;width:1200px;height:580px;overflow:hidden}
.hero .photo{position:absolute;inset:0;background:
  radial-gradient(ellipse 260px 300px at 640px 230px,#c49a7c 0%,rgba(196,154,124,.55) 40%,rgba(196,154,124,0) 100%),
  radial-gradient(ellipse 330px 240px at 660px 520px,#8e9398 0%,rgba(142,147,152,0) 100%),
  linear-gradient(90deg,#2f3a40 0%,#4d5a60 28%,#7a6f66 50%,#5a5452 72%,#2e2c2c 100%)}
.badge{position:absolute;left:100px;top:80px;width:280px;height:280px;border-radius:50%;background:var(--white);box-shadow:0 4px 20px rgba(0,0,0,.25);text-align:center}
.badge::after{content:"";position:absolute;inset:14px;border:2px dashed #bbb;border-radius:50%}
.badge .pct{margin-top:70px;display:flex;justify-content:center;align-items:center;gap:12px;font-family:"Montserrat",sans-serif;font-weight:800;font-size:62px;line-height:62px}
.badge .cert{font-family:"Montserrat",sans-serif;font-size:20px;letter-spacing:3px;margin-top:10px}
.badge .code{display:inline-block;margin-top:16px;background:var(--ink);color:var(--white);font-size:13px;font-weight:700;padding:7px 18px;letter-spacing:1px}
.dots{position:absolute;top:512px;left:580px;display:flex;gap:10px}
.dots i{width:10px;height:10px;border-radius:50%;background:rgba(255,255,255,.55)}
.dots i.on{background:var(--white)}

/* section title */
.sec-title{position:absolute;left:0;width:1200px;text-align:center;font-weight:700;font-size:40px;letter-spacing:1px}

/* categories */
.cats{top:972px;display:grid;grid-template-columns:repeat(4,244px);gap:16px;height:300px}
.cat{position:relative;height:300px}
.cat .photo{width:100%;height:100%}
.cat-label{position:absolute;left:24px;top:28px;width:196px;height:176px;border:2px solid var(--white);padding:22px 16px;color:var(--white);text-align:center}
.cat-label h3{font-size:24px;font-weight:700;letter-spacing:1px}
.cat-label p{font-size:12px;line-height:17px;margin-top:8px}
.cat-label .btn{display:inline-block;margin-top:12px;background:var(--white);color:var(--ink);font-size:12px;font-weight:700;padding:6px 16px;border-radius:14px}

/* welcome */
.welcome{position:absolute;top:1332px;left:0;width:1200px;height:448px;background:var(--dark);color:var(--white)}
.welcome h2{position:absolute;left:88px;top:38px;font-size:38px;line-height:50px;font-weight:700;letter-spacing:1px}
.welcome p{position:absolute;left:88px;top:158px;width:540px;font-size:14px;line-height:28px;color:#e0e0e0}
.welcome .btn{position:absolute;left:88px;top:340px;width:168px;height:52px;border:2px solid var(--white);border-radius:26px;text-align:center;line-height:48px;font-size:17px;color:var(--white)}
.welcome .frame{position:absolute;left:712px;top:48px;width:390px;height:360px;border:3px solid #cfcfcf;padding:12px}
.welcome .frame .photo{width:100%;height:100%}

/* products */
.tabs{top:1920px;height:40px;border-bottom:1px solid var(--line);display:flex;font-size:14px}
.tabs span{padding:10px 24px;color:var(--muted)}
.tabs span.on{border:1px solid var(--line);border-bottom:1px solid var(--white);color:var(--ink);margin-bottom:-1px}
.tabs .arrows{position:absolute;right:0;top:8px;display:flex;gap:10px}
.products{top:2000px;display:grid;grid-template-columns:repeat(4,244px);gap:16px}
.product{position:relative;text-align:center}
.product .photo{width:244px;height:312px}
.sale{position:absolute;left:8px;top:8px;background:var(--sale);color:var(--white);font-size:11px;font-weight:700;padding:2px 8px}
.pill{position:absolute;left:50%;top:140px;transform:translateX(-50%);background:var(--ink);color:var(--white);font-size:12px;font-weight:700;padding:8px 18px;border-radius:18px;white-space:nowrap}
.pill.light{background:rgba(255,255,255,.9);color:var(--ink)}
.tools{position:absolute;left:0;right:0;top:280px;height:32px;background:var(--white);display:flex;align-items:center;gap:12px;padding:0 10px}
.tools .stars{margin-left:auto;color:var(--star);font-size:14px;letter-spacing:1px;line-height:1}
.product h4{font-family:"Open Sans",sans-serif;font-weight:400;font-size:15px;color:var(--muted);margin-top:18px}
.product .price{font-size:20px;font-weight:600;margin-top:8px}

/* perks */
.perks{top:2424px;display:flex;justify-content:space-between}
.perk{width:272px;height:104px;border:1px solid var(--line);box-shadow:0 2px 8px rgba(0,0,0,.12);display:flex;align-items:center;gap:14px;padding:0 20px}
.perk h4{font-size:15px;font-weight:700;white-space:nowrap}
.perk p{font-size:11px;color:var(--muted);margin-top:3px}

/* blog */
.blog{position:absolute;top:2580px;left:0;width:1200px;height:560px;background:var(--soft)}
.posts{top:160px;display:grid;grid-template-columns:repeat(3,300px);gap:62px}
.post{text-align:center}
.post .photo{width:300px;height:200px}
.post h3{font-size:18px;font-weight:700;margin-top:20px}
.post .meta{font-size:11px;color:var(--muted);margin-top:8px}
.post p{font-size:12px;line-height:18px;color:var(--muted);margin-top:10px}

/* newsletter */
.news{position:absolute;top:3180px;left:0;width:1200px;height:360px;background:linear-gradient(90deg,#ffffff 0%,#f5f8ef 40%,#cdd9a3 100%)}
.news .photo{position:absolute;right:0;top:0;width:560px;height:360px;background:radial-gradient(ellipse at 60% 60%,#e8d24a 0%,#b8b83a 35%,rgba(160,180,90,0) 75%)}
.news h2{position:absolute;left:88px;top:82px;font-size:40px;font-weight:700}
.news .sub{position:absolute;left:200px;top:140px;font-size:17px}
.news .field{position:absolute;left:88px;top:190px;width:540px;height:56px;background:var(--white);border:1px solid var(--line);font-size:14px;color:var(--muted);padding:18px 20px}
.news .btn{position:absolute;left:110px;top:268px;width:214px;height:52px;border-radius:26px;background:var(--ink);color:var(--white);font-size:16px;font-weight:700;text-align:center;line-height:52px}

/* footer */
.footer{position:absolute;top:3588px;left:0;width:1200px;height:384px;background:var(--darker);color:#cfcfcf}
.fcol{position:absolute;top:40px;font-size:13px;line-height:21px}
.fcol h4{color:var(--white);font-size:19px;font-weight:700;margin-bottom:14px}
.copy{position:absolute;left:88px;top:348px;font-size:12px;color:#aaa}
.pay{position:absolute;right:88px;top:344px;display:flex;gap:8px}
.pay i{width:36px;height:22px;background:#e6e6e6;border-radius:3px}
</style>
</head>
<body>

<div class="topbar">
  <div class="lang"><span>English ▾</span><span>USD ▾</span></div>
  <div class="links">
    <span><svg width="12" height="12" viewBox="0 0 12 12"><circle cx="6" cy="4" r="3" fill="#6d6d6d"/><path d="M1 12c0-3 2-5 5-5s5 2 5 5z" fill="#6d6d6d"/></svg>Login Or Register</span>
    <span><svg width="14" height="12" viewBox="0 0 14 12"><rect x="0" y="2" width="9" height="7" fill="#6d6d6d"/><path d="M9 4h3l2 3v2H9z" fill="#6d6d6d"/></svg>Track Your Order</span>
    <span><svg width="12" height="12" viewBox="0 0 12 12"><rect x="1" y="4" width="10" height="8" fill="#6d6d6d"/><rect x="0" y="2" width="12" height="3" fill="#6d6d6d"/></svg>Gift Card</span>
  </div>
</div>

<header class="header">
  <div class="brand"><span class="brand-mark"></span><span class="brand-name">VANTOR</span></div>
  <div class="head-info offer">
    <svg width="30" height="30" viewBox="0 0 30 30"><rect x="3" y="12" width="24" height="16" fill="#1f1f1f"/><rect x="1" y="7" width="28" height="6" fill="#1f1f1f"/><rect x="13.5" y="7" width="3" height="21" fill="#fff"/></svg>
    <div>Special Offer<br><b>First orders $10 Off</b></div>
  </div>
  <div class="head-info cart">
    <svg width="30" height="30" viewBox="0 0 30 30"><path d="M2 5h5l4 15h14l3-11H9" fill="none" stroke="#1f1f1f" stroke-width="2.5"/><circle cx="12" cy="25" r="2.5" fill="#1f1f1f"/><circle cx="23" cy="25" r="2.5" fill="#1f1f1f"/></svg>
    <div>Shopping Cart<br><b>$0.00</b></div>
  </div>
</header>

<nav class="nav">
  <a class="active">Home</a><a>About Us</a><a>Shop</a><a>Product</a><a>Blog</a><a>Contact Us</a>
  <svg class="search" width="24" height="24" viewBox="0 0 24 24"><circle cx="10" cy="10" r="7" fill="none" stroke="#fff" stroke-width="3"/><path d="M15 15l7 7" stroke="#fff" stroke-width="3"/></svg>
</nav>

<section class="hero">
  <div class="photo" role="img" aria-label="Smiling athlete in a grey branded t-shirt standing in a gym"></div>
  <div class="badge">
    <div class="pct"><svg width="44" height="44" viewBox="0 0 30 30"><rect x="3" y="12" width="24" height="16" fill="#1f1f1f"/><rect x="1" y="7" width="28" height="6" fill="#1f1f1f"/><rect x="13.5" y="7" width="3" height="21" fill="#fff"/></svg>50%</div>
    <div class="cert">CERTIFICATE</div>
    <div class="code">PROMO CODE - GYM 500</div>
  </div>
  <div class="dots"><i class="on"></i><i></i><i></i></div>
</section>

<h2 class="sec-title" style="top:888px">TOP CATEGORIES</h2>
<div class="wrap cats">
  <div class="cat">
    <div class="photo" role="img" aria-label="Athlete training with a kettlebell" style="background:linear-gradient(135deg,#4a4a4a 0%,#1c1c1c 55%,#2e2e2e 100%)"></div>
    <div class="cat-label">
      <h3>SUPPLEMENT</h3>
      <p>Lorem ipsum dolor sit amet, consectetur adipiscing elit, sed do tempor.</p>
      <span class="btn">SHOP NOW</span>
    </div>
  </div>
  <div class="cat"><div class="photo" role="img" aria-label="Green herbal powder in a bowl with capsules" style="background:radial-gradient(ellipse at 40% 35%,#7f8a3a 0%,#8f8152 45%,#b9a27a 100%)"></div></div>
  <div class="cat"><div class="photo" role="img" aria-label="Pile of pale green capsules" style="background:linear-gradient(135deg,#e6e9dc 0%,#b7c09a 50%,#d8dcc8 100%)"></div></div>
  <div class="cat"><div class="photo" role="img" aria-label="Two black hooded sweatshirts on white" style="background:linear-gradient(90deg,#f4f4f4 0%,#2b2b2b 22%,#3a3a3a 45%,#ededed 50%,#2b2b2b 56%,#3a3a3a 80%,#f4f4f4 100%)"></div></div>
</div>

<section class="welcome">
  <h2>WELCOME TO VANTOR<br>WEAR AND FUEL.</h2>
  <p>Lorem ipsum dolor sit amet, consectetur adipiscing elit, sed do eiusmod tempor incididunt ut labore et dolore magna aliqua. Ut enim ad minim veniam, quis nostrud exercitation ullamco laboris nisi ut aliquip ex ea commodo consequat. Duis aute irure dolor in reprehenderit in voluptate velit.</p>
  <span class="btn">Read more</span>
  <div class="frame"><div class="photo" role="img" aria-label="Athlete holding a shaker bottle beside a supplement tub" style="background:linear-gradient(135deg,#e4e4e4 0%,#b8a292 50%,#8c3a30 100%)"></div></div>
</section>

<h2 class="sec-title" style="top:1826px">FEATURE PRODUCTS</h2>
<div class="wrap tabs">
  <span class="on">Latest</span><span>Supplement</span><span>Clothing</span>
  <div class="arrows">
    <svg width="20" height="20" viewBox="0 0 20 20"><circle cx="10" cy="10" r="10" fill="#3a3a3a"/><path d="M12 5l-5 5 5 5" fill="none" stroke="#fff" stroke-width="2"/></svg>
    <svg width="20" height="20" viewBox="0 0 20 20"><circle cx="10" cy="10" r="10" fill="#3a3a3a"/><path d="M8 5l5 5-5 5" fill="none" stroke="#fff" stroke-width="2"/></svg>
  </div>
</div>
<div class="wrap products">
  <div class="product">
    <div class="photo" role="img" aria-label="Model wearing a yellow hoodie" style="background:linear-gradient(160deg,#e8e4dc 0%,#d8c9a8 50%,#e3c45a 100%)"></div>
    <span class="sale">SALE</span>
    <span class="pill">● QUICK VIEW</span>
    <div class="tools">
      <svg width="14" height="14" viewBox="0 0 14 14"><path d="M1 2h2l2 7h7l1-5H4" fill="none" stroke="#1f1f1f" stroke-width="1.6"/></svg>
      <svg width="14" height="14" viewBox="0 0 14 14"><path d="M7 12L2 7a3 3 0 015-4 3 3 0 015 4z" fill="#1f1f1f"/></svg>
      <svg width="14" height="14" viewBox="0 0 14 14"><path d="M3 4h9M3 7h9M3 10h9" stroke="#1f1f1f" stroke-width="1.6"/></svg>
      <span class="stars">★★★★★</span>
    </div>
    <h4>YELLOW HOODIE</h4><div class="price">$520.00</div>
  </div>
  <div class="product">
    <div class="photo" role="img" aria-label="Supplement tablet bottle on yellow" style="background:linear-gradient(160deg,#f4d23a,#f0e6a0)"></div>
    <h4>SUPPLEMENT TABLETS</h4><div class="price">$620.00</div>
  </div>
  <div class="product">
    <div class="photo" role="img" aria-label="Supplement powder tub on dark background" style="background:linear-gradient(160deg,#2c2c2c,#111)"></div>
    <span class="pill light">SOLD OUT</span>
    <h4>SUPPLEMENT POWDER</h4><div class="price">$420.00</div>
  </div>
  <div class="product">
    <div class="photo" role="img" aria-label="Man wearing a black t-shirt" style="background:linear-gradient(160deg,#b5b5b5,#5c5c5c)"></div>
    <h4>T SHIRT</h4><div class="price">$700.00</div>
  </div>
</div>

<div class="wrap perks">
  <div class="perk">
    <svg width="40" height="30" viewBox="0 0 40 30"><rect x="1" y="3" width="38" height="24" rx="3" fill="none" stroke="#1f1f1f" stroke-width="2.5"/><rect x="1" y="9" width="38" height="5" fill="#1f1f1f"/></svg>
    <div><h4>SECURE PAYMENTS</h4><p>FULL PAYMENT SECURE</p></div>
  </div>
  <div class="perk">
    <svg width="42" height="30" viewBox="0 0 42 30"><rect x="1" y="4" width="25" height="18" fill="#1f1f1f"/><path d="M26 10h9l6 7v5H26z" fill="#1f1f1f"/><circle cx="9" cy="25" r="4" fill="#1f1f1f" stroke="#fff" stroke-width="2"/><circle cx="33" cy="25" r="4" fill="#1f1f1f" stroke="#fff" stroke-width="2"/></svg>
    <div><h4>WORLDWIDE SHIPPING</h4><p>SHIPPING ORDER OVER $2000</p></div>
  </div>
  <div class="perk">
    <svg width="36" height="32" viewBox="0 0 36 32"><path d="M2 2h16l16 16-14 12L2 16z" fill="#1f1f1f"/><circle cx="9" cy="9" r="3" fill="#fff"/></svg>
    <div><h4>MEMBER DISCOUNT</h4><p>20% OFF FOR ALL REGISTER USER</p></div>
  </div>
</div>

<section class="blog">
  <h2 class="sec-title" style="top:46px">LATEST FROM OUR BLOG</h2>
  <div class="wrap posts">
    <div class="post">
      <div class="photo" role="img" aria-label="Athlete drinking a protein shake" style="background:linear-gradient(135deg,#e6e2da,#7b6f62)"></div>
      <h3>LOREM IPSUM DOLOR</h3>
      <div class="meta">▦ SEPTEMBER 04, 2019 | ✎ 12 COMMENTS</div>
      <p>Lorem ipsum dolor sit amet, consectetur adipiscing elit, sed do eiusmod tempor incididunt ut labore et dolore magna aliqua.</p>
    </div>
    <div class="post">
      <div class="photo" role="img" aria-label="Boxer in fighting stance on black background" style="background:linear-gradient(135deg,#3a3a3a,#0d0d0d)"></div>
      <h3>LOREM IPSUM DOLOR</h3>
      <div class="meta">▦ SEPTEMBER 04, 2019 | ✎ 12 COMMENTS</div>
      <p>Lorem ipsum dolor sit amet, consectetur adipiscing elit, sed do eiusmod tempor incididunt ut labore et dolore magna aliqua.</p>
    </div>
    <div class="post">
      <div class="photo" role="img" aria-label="Muscular athlete posing on dark background" style="background:linear-gradient(135deg,#4a3428,#120c09)"></div>
      <h3>LOREM IPSUM DOLOR</h3>
      <div class="meta">▦ SEPTEMBER 04, 2019 | ✎ 12 COMMENTS</div>
      <p>Lorem ipsum dolor sit amet, consectetur adipiscing elit, sed do eiusmod tempor incididunt ut labore et dolore magna aliqua.</p>
    </div>
  </div>
</section>

<section class="news">
  <div class="photo" role="img" aria-label="Golden supplement softgel capsules"></div>
  <h2>JOIN OUR NEWSLETTER</h2>
  <div class="sub">Get Latest News &amp; Update</div>
  <div class="field">Enter the email</div>
  <span class="btn">SUBSCRIBE NOW</span>
</section>

<footer class="footer">
  <div class="fcol" style="left:88px;width:300px">
    <h4>Contact us</h4>
    12 Kestrel Lane, Unit 4, Brookfield Park,<br>Northvale Junction, Harbor Road,<br>Northvale 10482<br>hello@vantorwear.shop<br>555-0148-220
  </div>
  <div class="fcol" style="left:480px">
    <h4>Quick links</h4>Home<br>About Us<br>Shop<br>Product<br>Blog<br>Contact Us
  </div>
  <div class="fcol" style="left:720px">
    <h4>Help</h4>Gift Cards<br>Order Status<br>Free Shipping<br>Customer<br>International
  </div>
  <div class="fcol" style="left:956px">
    <h4>Other Links</h4>Faq<br>Payment Method<br>How To Track<br>Shipping Info<br>Free Membership
  </div>
  <div class="copy">© 2019 Copyright: Vantor Wear and Fuel All Rights Reserved</div>
  <div class="pay"><i></i><i></i><i></i><i></i><i></i><i></i></div>
</footer>

</body>
</html>
```